Wallaby and Rabbit deterrent flyer

I am after a one page flyer for the advertisement of a rabbit and wallaby deterrent. I am doing some targeted advertising of a product that deters rabbits and wallabies from eating plants
Title Possum and Deer away
Few pointers i want to hit are:
Guaranteed to prevent animals from eating your plants for up to one month
Rain Fast
All natural
Having trouble with rabbits and wallabies eating your garden look no further
needs to sound like i provide the service of spraying
the product for the customers
Book before August 15 and receive $10 off
Contact Brent at Blue Ridge Lawn Fella
04yyyyyyyy
My business card is also attached if it could match it
UPDATE: Change in title to Possum, Deer and Hare away
Gardener

```html
<!DOCTYPE html>
<html lang="en">
<head>
<meta charset="utf-8">
<title>Possum and Deer Away – Flyer</title>
<link rel="stylesheet" href="https://fonts.googleapis.com/css2?family=Alfa+Slab+One&family=Arvo:ital,wght@0,700;1,400&display=swap">
<style>
  :root {
    --green: #6aa821;
    --green-dark: #4f8a12;
    --green-light: #cfe6a8;
    --orange: #f0a020;
    --paper: #ffffff;
    --mist: #e6ebe6;
    --backdrop: #ecebe7;
    --grass-top: #b9dc86;
    --grass-bottom: #4d8f1c;
  }
  * { margin: 0; padding: 0; box-sizing: border-box; }
  html, body { width: 1200px; height: 1000px; overflow: hidden; }
  body {
    background: var(--backdrop);
    display: flex; align-items: center; justify-content: center;
    font-family: "Arvo", Georgia, serif;
  }
  .flyer {
    position: relative;
    width: 440px; height: 920px;
    background: linear-gradient(180deg, var(--paper) 0%, var(--mist) 55%);
    overflow: hidden;
    box-shadow: 0 6px 18px rgba(0,0,0,.18);
  }
  .headline {
    position: absolute; top: 26px; left: 0; right: 24px;
    text-align: right;
    font-family: "Alfa Slab One", Georgia, serif;
    color: var(--green);
    line-height: .95;
    text-transform: uppercase;
  }
  .headline .line-1 { display: block; font-size: 66px; }
  .headline .line-2 { display: block; font-size: 54px; }
  .headline .big-word {
    display: block; margin-top: 6px;
    font-size: 128px; color: var(--orange);
    letter-spacing: -2px;
  }
  .photo { position: absolute; }
  .photo--grass {
    left: 0; right: 0; top: 440px; bottom: 0;
    background: linear-gradient(180deg, var(--grass-top) 0%, #86bf4c 40%, var(--grass-bottom) 100%);
  }
  .photo--wallaby {
    left: 200px; top: 330px; width: 220px; height: 510px;
    border-radius: 90px 90px 20px 20px;
    background: linear-gradient(180deg, #8c8580 0%, #b3aca6 50%, #8a837e 100%);
  }
  .photo--rabbit {
    left: 150px; top: 610px; width: 170px; height: 230px;
    border-radius: 70px 70px 20px 20px;
    background: linear-gradient(180deg, #d9b486 0%, #c2966a 100%);
  }
  .pitch {
    position: absolute; left: 18px; top: 330px; width: 190px;
    text-align: right; color: var(--green);
    font-size: 15px; line-height: 1.2; font-weight: 700;
  }
  .stroke {
    position: absolute; left: 30px; top: 448px;
  }
  .offer {
    position: absolute; left: 10px; top: 478px; width: 200px;
    text-align: right; color: var(--green-dark);
    font-size: 21px; line-height: 1.1; font-weight: 700;
    text-shadow: 0 0 4px #fff, 0 0 2px #fff;
  }
  .offer .discount {
    display: block; color: var(--orange);
    font-family: "Alfa Slab One", Georgia, serif;
    font-size: 30px; font-weight: 400;
  }
  .badge {
    position: absolute; left: 30px; top: 620px; width: 160px; height: 160px;
  }
  .badge-text {
    position: absolute; left: 30px; top: 652px; width: 160px;
    text-align: center; color: var(--green-dark);
    font-size: 21px; line-height: 1.1; font-weight: 700;
  }
  .contact-bar {
    position: absolute; left: 0; right: 0; bottom: 0; height: 84px;
    background: var(--green);
    color: #fff;
    display: flex; align-items: center; justify-content: space-between;
    padding: 0 18px;
  }
  .contact-name { font-size: 19px; font-weight: 700; line-height: 1.1; }
  .contact-business { display: block; font-size: 12px; font-weight: 400; font-style: italic; }
  .contact-phone { font-size: 32px; font-weight: 700; }
</style>
</head>
<body>
  <main class="flyer">
    <div class="photo photo--grass" role="img" aria-label="Photo of lush green lawn grass"></div>
    <div class="photo photo--wallaby" role="img" aria-label="Photo of a grey wallaby sitting upright"></div>
    <div class="photo photo--rabbit" role="img" aria-label="Photo of a tan rabbit sitting on grass"></div>

    <h1 class="headline">
      <span class="line-1">Possum</span>
      <span class="line-2">and Deer</span>
      <span class="big-word">Away</span>
    </h1>

    <p class="pitch">Guaranteed to prevent animals from eating your plants for up to one month</p>

    <svg class="stroke" width="170" height="22" viewBox="0 0 170 22" aria-hidden="true">
      <path d="M4 14 C50 2,120 4,166 10 C120 12,60 14,4 18 Z" fill="var(--orange)"/>
    </svg>

    <p class="offer">Book before August 15 and receive <span class="discount">$10 OFF</span></p>

    <svg class="badge" viewBox="0 0 160 160" aria-hidden="true">
      <circle cx="80" cy="80" r="76" fill="var(--green-light)"/>
      <circle cx="80" cy="80" r="64" fill="#eaf5d8"/>
    </svg>
    <p class="badge-text">All<br>Natural<br>Rain<br>Fast</p>

    <footer class="contact-bar">
      <p class="contact-name">Contact Brent at
        <span class="contact-business">Blue Ridge Lawn Fella</span>
      </p>
      <p class="contact-phone">04yyyyyyyy</p>
    </footer>
  </main>
</body>
</html>
```